Valdane Companies Business Card Design

We need a new business card for our Private Equity Real Estate Development firm, “Valdane” and our EB-5 regional center “Thornmere Regional Center” on one card. We prefer a design that is simple, elegant, and represents the luxury products we design and build as well as the financial security and stability our successful history has produced. We are an industry leader in our field and 3rd generation family business that has evolved into an institutional quality investment platform. Considered design size is standard business card dimensions (3.5 x 2 inches with an additional 1/8 inch space for design elements or backgrounds that extend beyond the finished size of your piece.

Target Market(s)

• High net worth individuals
• Highly skilled technical workers and physicians in the US seeking investment-based immigration opportunities
• Sophisticated private equity investors
• Intermediary partners include domestic attorneys and investment brokers, as well as international agent networks
• US real estate developers

Industry/Entity Type

Finance

Contact Information for Business Card

(Providing placeholder info for personal information, please design for longer character spaces, longer names and addresses etc..)
• Logo for Valdane
• Logo for Thornmere Regional Center
• Full name: Marcus Valdane
• Job title: CEO
• Email address: mvaldane@valdanecompanies.com
• Cell phone number: +1.555.314.2287
• Office number +1.555.628.4410
• Office address: Larkfield Court 5, 4817 Vista Orilla, Briarholt, ST.
• Website: www.valdanecompanies.com

Font styles to use
Serif
Sans Serif

Colors
ec1f27
ffffff
000000

Requirements
Must have
• • Logo for Valdane
• • Logo for Thornmere Regional Center
• - Use rounded corners
• (See .ai file included for logos)
Nice to have
• • Simple, elegant design
• • Aesthetically compatible with our website design (www.valdanecompanies.com)
• • Color palette including but not limited to white, black, and red (as per logos)
Should not have
• - Not too much red color
• - Do not stack both logos on top of each other

```html
<!DOCTYPE html>
<html lang="en">
<head>
<meta charset="utf-8">
<title>Valdane Companies Business Card</title>
<link href="https://fonts.googleapis.com/css2?family=Work+Sans:wght@400;500;600&display=swap" rel="stylesheet">
<style>
  :root {
    --stage: #1c1c1c;
    --card-black: #0d0d0d;
    --card-white: #ffffff;
    --brand-red: #9e0f1d;
    --silver: #c9c9c9;
    --ink: #4a4a4a;
  }
  * { box-sizing: border-box; margin: 0; padding: 0; }
  html, body { width: 1200px; height: 800px; overflow: hidden; }
  body {
    background: var(--stage);
    font-family: "Work Sans", Arial, sans-serif;
    position: relative;
  }
  .card {
    position: absolute;
    left: 294px;
    width: 612px;
    height: 350px;
    border-radius: 20px;
    overflow: hidden;
  }
  .card--back { top: 35px; background: var(--card-black); }
  .card--front { top: 415px; background: var(--card-white); }

  /* back */
  .back-mark {
    position: absolute; left: 110px; top: 140px;
    display: flex; align-items: center; gap: 18px;
  }
  .back-mark .mark-square { width: 56px; height: 56px; background: var(--silver); }
  .back-mark .divider { width: 1px; height: 66px; background: var(--silver); }
  .back-mark .wordmark { color: #ffffff; font-weight: 600; }
  .back-mark .wordmark .name { font-size: 40px; letter-spacing: 1px; line-height: 1; }
  .back-mark .wordmark .sub { font-size: 13px; letter-spacing: 8px; margin-top: 6px; }
  .back-corner {
    position: absolute; right: 36px; top: 36px; text-align: right;
    color: var(--brand-red); font-weight: 600;
  }
  .back-corner .name { font-size: 20px; letter-spacing: 1px; }
  .back-corner .sub { font-size: 7px; letter-spacing: 4px; margin-top: 2px; }

  /* front */
  .name-band {
    position: absolute; left: 0; top: 42px; width: 292px; height: 64px;
    background: var(--brand-red); color: #ffffff; padding: 10px 0 0 36px;
  }
  .name-band .person { font-size: 20px; font-weight: 500; letter-spacing: 1px; }
  .name-band .role { font-size: 12px; margin-top: 4px; letter-spacing: 0.5px; }
  .front-mark {
    position: absolute; right: 56px; top: 36px;
    display: flex; flex-direction: column; align-items: center;
    color: var(--brand-red); font-weight: 600;
  }
  .front-mark .mark-square { width: 50px; height: 50px; background: var(--brand-red); margin-bottom: 14px; }
  .front-mark .name { font-size: 32px; letter-spacing: 1px; line-height: 1; }
  .front-mark .sub { font-size: 10px; letter-spacing: 6px; margin-top: 6px; }

  .contact {
    position: absolute; left: 36px; bottom: 34px;
    list-style: none; font-size: 14px; color: var(--ink); line-height: 20px;
  }
  .contact li { display: flex; align-items: center; gap: 8px; }
  .contact svg { width: 10px; height: 10px; fill: var(--brand-red); }
  .contact .web { color: var(--brand-red); font-weight: 500; letter-spacing: 0.5px; }
  .address {
    position: absolute; right: 56px; bottom: 44px;
    font-size: 14px; color: var(--ink); line-height: 19px; font-style: normal;
  }
  .address .company { color: var(--brand-red); font-weight: 600; font-size: 13px; margin-bottom: 4px; }
</style>
</head>
<body>
  <section class="card card--back">
    <div class="back-corner">
      <div class="name">THORNMERE</div>
      <div class="sub">REGIONAL CENTER</div>
    </div>
    <div class="back-mark">
      <span class="mark-square"></span>
      <span class="divider"></span>
      <div class="wordmark">
        <div class="name">THORNMERE</div>
        <div class="sub">REGIONAL CENTER</div>
      </div>
    </div>
  </section>

  <section class="card card--front">
    <div class="name-band">
      <div class="person">MARCUS VALDANE</div>
      <div class="role">CEO</div>
    </div>
    <div class="front-mark">
      <span class="mark-square"></span>
      <div class="name">THORNMERE</div>
      <div class="sub">REGIONAL CENTER</div>
    </div>
    <ul class="contact">
      <li><svg viewBox="0 0 10 10"><path d="M2 0h2l1 3-1.5 1a6 6 0 0 0 2.5 2.5L7 5l3 1v2a2 2 0 0 1-2 2A8 8 0 0 1 0 2a2 2 0 0 1 2-2z"/></svg>+1.555.314.2287</li>
      <li><svg viewBox="0 0 10 10"><path d="M2.5 0h5a1 1 0 0 1 1 1v8a1 1 0 0 1-1 1h-5a1 1 0 0 1-1-1V1a1 1 0 0 1 1-1zm.5 1.5v6h4v-6z"/></svg>+1.555.628.4410</li>
      <li><svg viewBox="0 0 10 10"><path d="M0 2h10v6H0zm1 1v.3l4 2.5 4-2.5V3zm0 1.5V7h8V4.5L5 7z"/></svg>mvaldane@valdanecompanies.com</li>
      <li class="web">www. valdanecompanies.com</li>
    </ul>
    <address class="address">
      <div class="company">VALDANE COMPANIES, LLC</div>
      Larkfield Court 5,4817<br>
      Vista Orilla<br>
      Briarholt, ST
    </address>
  </section>
</body>
</html>
```